Wordpress website design for a high-end painting business

We are currently rebranding and are looking to update our Wordpress theme. We have recently rebranded our logo on PixelHarbor, and would like our website to be equally as refined.
Our business is named “Fenwick Painters”. We are a high-end painting business that is known for being professional and having high standards. Our clean and professional image is important as it separates us from our competition. Our current website can be found at www.fenwickcoatings.co.nz . We designed the site ourselves so it is understandably rudimentary. We are generally happy with the. page layout of our existing site, but we like a professional remodel. Any ideas on improvement welcomed.
We would like the front page of the website to summarise all of the info throughout the whole website (I.e introduction, photos, testimonials, contact info etc.) as visitors typically scroll through the first page to see that we are reputable and get to our contact number/email contact at the bottom of the page. We would like this first page to give a clean well rounded image of our business. We would like the gallery to be a scroll through of large photos, as it is difficult to see paint details in smaller photos. A contact page with an enquiry section would also be good.
For the colour scheme, we would like something that fits a bold, masculine and high end theme (similar to our logo attached).
We would like the footer to include Velmora paint logos and the accredited painter logo we have included as these are important to our profession.
We have attached some photos of our work also. I will add more in the coming days. More can also be found on our website.
If you have questions or comments, please don’t hesitate to ask and I will get back as soon as possible.
We are open to your own interpretation or ideas for a better layout/site provided they fit the general brief of being a well rounded site for our profession.
Thanks,
Fenwick Painters.
Target Market(s)
High end clients
Industry/Entity Type
Painting (interior and exterior)
Coding
Coded - Design and coding required
Requirements
Must have
- Classy feel, separating us from typical painting companies. Well rounded homepage.
Nice to have
- Lots of examples of our work
Should not have
- Untidy paint motifs (eg, paint droplets, paint splashes)

```html
<!DOCTYPE html>
<html lang="en">
<head>
<meta charset="utf-8">
<title>Fenwick Painters</title>
<link href="https://fonts.googleapis.com/css2?family=Open+Sans:ital,wght@0,400;0,600;0,700;1,400&family=Poppins:wght@400;500&display=swap" rel="stylesheet">
<style>
:root{
  --brown:#7a5a33;
  --navy:#171c27;
  --ink:#1d2029;
  --text:#3b3b3b;
  --white:#ffffff;
  --muted:#555;
}
*{margin:0;padding:0;box-sizing:border-box}
html,body{width:1200px;height:3188px;overflow:hidden;background:var(--white)}
body{position:relative;font-family:"Open Sans",sans-serif;color:var(--text)}
.abs{position:absolute}

/* hero */
.hero{left:0;top:0;width:1200px;height:728px;
  background:linear-gradient(180deg,#5f8fc9 0%,#9fbde0 14%,#b9a987 30%,#a89a78 48%,#8c7f62 58%,#6f8a3e 70%,#5c7d33 100%)}
.brand{left:111px;top:24px;width:112px;text-align:center;color:var(--navy)}
.brand-mark{width:70px;height:70px;border-radius:50%;background:var(--navy);margin:0 auto 10px}
.brand-name{font-weight:700;font-size:17px;line-height:1.1;letter-spacing:.5px}
.nav{left:341px;top:45px;display:flex;gap:0}
.nav a{color:var(--white);text-decoration:none;font-size:14px;font-weight:600;margin-right:26px;position:relative}
.nav a.active:after{content:"";position:absolute;left:0;right:0;bottom:-10px;height:4px;background:var(--white);border-radius:2px}
.btn-dark{background:var(--navy);color:var(--white);font-weight:700;font-size:14px;border-radius:24px;display:flex;align-items:center;justify-content:center}
.nav-quote{left:923px;top:38px;width:164px;height:45px}
.hero-band{left:272px;top:273px;width:660px;height:188px;background:rgba(40,36,30,.55)}
.hero-title{left:0;width:1200px;top:286px;text-align:center;color:var(--white);font-size:74px;font-weight:700;letter-spacing:1px}
.hero-quote{left:517px;top:381px;width:166px;height:42px}
.scroll-down{left:568px;top:696px;width:64px;height:64px;border-radius:50%;background:var(--white)}

/* welcome */
.eyebrow{left:0;width:1200px;top:808px;text-align:center;color:var(--brown);font-weight:700;font-size:21px}
.section-title{left:0;width:1200px;text-align:center;color:var(--ink);font-weight:700;font-size:45px}
.welcome-title{top:840px}
.emblem{left:111px;top:909px;width:477px;height:384px}
.emblem-circle{left:120px;top:34px;width:316px;height:316px;border-radius:50%;background:var(--navy)}
.emblem-name{left:0;top:176px;width:556px;text-align:center;color:var(--brown);font-weight:700;font-size:30px}
.intro{left:599px;top:922px;width:488px;font-size:15px;line-height:25.8px;text-align:justify}
.intro p+p{margin-top:25.8px}
.btn-brown{left:599px;top:1222px;width:164px;height:44px;background:var(--brown);color:var(--white);font-weight:700;font-size:14px;border-radius:24px;display:flex;align-items:center;justify-content:center;gap:5px}

/* gallery */
.gallery-title{top:1366px}
.tile{position:absolute}
.t1{left:0;top:1445px;width:400px;height:557px;background:linear-gradient(180deg,#2a2a2a 0%,#cfd0d2 30%,#a9abae 100%)}
.t2{left:400px;top:1445px;width:800px;height:278px;background:linear-gradient(90deg,#e7d7b9 0%,#f0e2c6 50%,#bfe0d6 80%,#a9d3c8 100%)}
.t3{left:400px;top:1723px;width:400px;height:279px;background:linear-gradient(180deg,#6d7a82 0%,#9aa2a2 40%,#4d6a33 100%)}
.t4{left:800px;top:1723px;width:400px;height:556px;background:linear-gradient(120deg,#efe6d4 0%,#c8bc90 50%,#8e8562 100%)}
.t5{left:0;top:2002px;width:800px;height:277px;background:linear-gradient(180deg,#2f7fd8 0%,#76a9e2 40%,#8a8f94 65%,#5a7f36 100%)}
.zoom{left:571px;top:1833px;width:58px;height:58px;border-radius:50%;background:var(--white)}

/* testimonials */
.testi-title{top:2354px}
.quote{position:absolute;width:306px;text-align:center}
.quote-mark{font-family:Georgia,serif;font-size:64px;font-weight:700;color:var(--ink);line-height:40px;height:40px;margin-top:2px}
.quote-text{margin-top:24px;font-style:italic;font-size:14px;line-height:21.4px;color:var(--muted);text-align:justify;text-align-last:center}
.quote-name{margin-top:14px;font-weight:700;font-size:14px;color:var(--ink)}
.quote-year{margin-top:6px;font-weight:700;font-size:14px;color:var(--brown)}
.q1{left:111px;top:2470px}.q2{left:447px;top:2470px}.q3{left:782px;top:2470px}
.arrow{top:2586px}

/* footer */
.footer{left:0;top:2837px;width:1200px;height:351px;background:var(--navy);font-family:"Poppins",sans-serif}
.contact{position:absolute;top:84px;width:330px;text-align:center}
.contact-icon{width:54px;height:54px;border-radius:50%;background:var(--brown);margin:0 auto;display:flex;align-items:center;justify-content:center}
.contact-label{margin-top:12px;color:var(--brown);font-weight:500;font-size:18px}
.contact-value{margin-top:4px;color:var(--white);font-size:19px}
.c1{left:96px}.c2{left:423px}.c3{left:754px}
.badge{position:absolute;top:268px;height:26px}
.b1{left:111px;width:88px;background:#1b3a8c;border-radius:2px}
.b2{left:220px;width:213px;background:#2a7fd0;border-radius:2px}
.copyright{position:absolute;right:113px;top:270px;color:var(--white);font-size:15px}
</style>
</head>
<body>

<header>
  <div class="abs hero" role="img" aria-label="Photograph of a large two-storey painted house with garden and lawn"></div>
  <div class="abs brand">
    <div class="brand-mark"></div>
    <div class="brand-name">FENWICK PAINTERS</div>
  </div>
  <nav class="abs nav">
    <a class="active" href="#">HOME</a><a href="#">SERVICES</a><a href="#">GALLERY</a><a href="#">ABOUT</a><a href="#">CONTACT</a><a href="#">ALL TESTIMONIALS</a>
  </nav>
  <a class="abs btn-dark nav-quote">GET A QUOTE</a>
  <div class="abs hero-band"></div>
  <h1 class="abs hero-title">FENWICK PAINTER</h1>
  <a class="abs btn-dark hero-quote">GET A QUOTE</a>
  <div class="abs scroll-down">
    <svg width="64" height="64" viewBox="0 0 64 64"><path d="M20 20 L32 33 L44 20 M20 31 L32 44 L44 31" fill="none" stroke="#171c27" stroke-width="3"/></svg>
  </div>
</header>

<section>
  <div class="abs eyebrow">WELCOME TO</div>
  <h2 class="abs section-title welcome-title">FENWICK PAINTER</h2>
  <div class="abs emblem">
    <div class="abs emblem-circle"></div>
    <div class="abs emblem-name" style="color:#fff">Fenwick Painters</div>
  </div>
  <div class="abs intro">
    <p>Here at Fenwick Painters, we take a lot of pride in our work. We strive to ensure the highest quality paint-work, paying close attention to detail to provide a long lasting finish. Our clients are always our priority, we aim to deliver beyond their expectations.It is our goal to provide an excellent service from start to finish through clear communication, free quoting and transparency with our pricing.</p>
    <p>We take great pride in the preparation of surfaces for painting and only use the best quality products to ensure we achieve the best finish for you. Our qualified interior designer can also assist you with your colour selection as a part of our free colour consultancy service.</p>
  </div>
  <a class="abs btn-brown">LEARN MORE
    <svg width="13" height="13" viewBox="0 0 13 13"><circle cx="6.5" cy="6.5" r="6.5" fill="#fff"/><path d="M4 6.5h5M6.5 4l2.5 2.5L6.5 9" stroke="#7a5a33" stroke-width="1.6" fill="none"/></svg>
  </a>
</section>

<section>
  <h2 class="abs section-title gallery-title">GALLERY</h2>
  <div class="tile t1" role="img" aria-label="Photo of a freshly painted white commercial interior with linear ceiling lights"></div>
  <div class="tile t2" role="img" aria-label="Photo of an empty room painted cream and mint green with glass doors"></div>
  <div class="tile t3" role="img" aria-label="Photo of a repainted grey single-storey house exterior"></div>
  <div class="tile t4" role="img" aria-label="Photo of a painted stairwell with white balustrade and doors"></div>
  <div class="tile t5" role="img" aria-label="Photo of a modern house exterior with white and grey cladding"></div>
  <div class="abs zoom">
    <svg width="58" height="58" viewBox="0 0 58 58"><path d="M29 20v18M20 29h18" stroke="#171c27" stroke-width="2.5"/></svg>
  </div>
</section>

<section>
  <h2 class="abs section-title testi-title">TESTIMONIALS</h2>
  <svg class="abs arrow" style="left:44px" width="22" height="32" viewBox="0 0 22 32"><path d="M16 4 L6 16 L16 28" fill="none" stroke="#1d2029" stroke-width="3"/></svg>
  <svg class="abs arrow" style="left:1130px" width="22" height="32" viewBox="0 0 22 32"><path d="M6 4 L16 16 L6 28" fill="none" stroke="#1d2029" stroke-width="3"/></svg>
  <div class="quote q1">
    <div class="quote-mark">&ldquo;</div>
    <p class="quote-text">“Marcus and his Team have done an amazing job painting our house. Without a doubt hiring them was our best decision. Attention to detail, great communication, respect towards our needs, working within the budget are just a few things to describe them. I will be recommending Fenwick Painters and Decorators for many years to come. Thank you, Guys!”</p>
    <div class="quote-name">HELENA MARSH</div>
    <div class="quote-year">(2019)</div>
  </div>
  <div class="quote q2">
    <div class="quote-mark">&ldquo;</div>
    <p class="quote-text">“These guys are great from beginning to end. Very professional, excellent businessmen, hard workers, and top-quality work. Excellent communication, do what they say they will do and more, and really go the extra mile to make the job as painless as possible. Without reservations would highly recommend!”</p>
    <div class="quote-name">CLARA DUNMORE</div>
    <div class="quote-year">(2020)</div>
  </div>
  <div class="quote q3">
    <div class="quote-mark">&ldquo;</div>
    <p class="quote-text">“Just had our house interior painted throughout by Fenwicks. They were professional right from the start. They turned up to give a quote when other firms never responded. They were spot on with their time and cost estimates and never missed a day ..we had to ask them not to work on Public Holidays. They have an attention to detail and a level of care that is above”</p>
    <div class="quote-name">OWEN TATE</div>
    <div class="quote-year">(2020)</div>
  </div>
</section>

<footer class="abs footer">
  <div class="contact c1">
    <div class="contact-icon"><svg width="24" height="24" viewBox="0 0 24 24"><path d="M12 22s-7-7-7-12a7 7 0 0 1 14 0c0 5-7 12-7 12z" fill="none" stroke="#fff" stroke-width="1.6"/><circle cx="12" cy="10" r="2.5" fill="none" stroke="#fff" stroke-width="1.6"/></svg></div>
    <div class="contact-label">Address :</div>
    <div class="contact-value">12 Kowhai Lane, Ashgrove</div>
  </div>
  <div class="contact c2">
    <div class="contact-icon"><svg width="24" height="24" viewBox="0 0 24 24"><path d="M6 3l3 4-2 2a11 11 0 0 0 8 8l2-2 4 3-2 3C11 21 3 13 3 5z" fill="none" stroke="#fff" stroke-width="1.5"/></svg></div>
    <div class="contact-label">Phone :</div>
    <div class="contact-value">021 555 0148</div>
  </div>
  <div class="contact c3">
    <div class="contact-icon"><svg width="24" height="24" viewBox="0 0 24 24"><rect x="3" y="6" width="18" height="12" fill="none" stroke="#fff" stroke-width="1.5"/><path d="M3 6l9 7 9-7" fill="none" stroke="#fff" stroke-width="1.5"/></svg></div>
    <div class="contact-label">Email address :</div>
    <div class="contact-value">fenwickpainters@mail.co.nz</div>
  </div>
  <div class="badge b1" role="img" aria-label="Velmora paint badge"></div>
  <div class="badge b2" role="img" aria-label="Velmora accredited painter badge"></div>
  <div class="copyright">© Copyrights 2022 Company name | All Rights Reserved</div>
</footer>

</body>
</html>
```